dobbo's business card for earthmoving and tipper hire business.

I have a small earthmoving and tipper truck company. I am aiming for the smaller jobs that the big guys don't want. I am also Doing grass slashing and fire hazard reduction work. I would like to see some earthy colors, greens browns etc. I have a tractor with a front end loader attachment, and a 22 ton tipper. I would like to maybe have a silhouette of a tipper and tractor/slasher/loader setup in centre with my business name over the top and details to one side or something like that

Industry/Entity Type

Business

Contact Information for Business Card

Dobbo's small earthworks and tipper hireToowoombaABN: 47781050480PH 0479126773Email dobbo.3@farrowpost.com

Font styles to use
Sans Serif

Colors
fbee3d
abd036
85cae6
f78f20

Requirements
Nice to have
• Earthy colors . business name in blue

```html
<!DOCTYPE html>
<html lang="en">
<head>
<meta charset="utf-8">
<title>Dobbo's Earthworks and Tipper Hire – Business Card</title>
<link rel="stylesheet" href="https://fonts.googleapis.com/css2?family=Lato:wght@700;900&family=Josefin+Sans:wght@400;600&family=Poppins:wght@500;600&family=Roboto:ital,wght@1,900&display=swap">
<style>
  :root {
    --rust: #93301f;
    --rust-dark: #6e2616;
    --field-green: #27a046;
    --band-green: #4f9a45;
    --olive: #877c47;
    --panel-green: #64984b;
    --ink-green: #263d1d;
    --sky: #b9dcec;
    --cream: #f4efe2;
    --base-grey: #4a4440;
  }
  * { margin: 0; padding: 0; box-sizing: border-box; }
  html, body { width: 1200px; height: 741px; overflow: hidden; background: #ffffff; }
  .card { position: relative; width: 1200px; height: 741px; overflow: hidden; background: var(--rust); }
  .card-backdrop { position: absolute; inset: 0; }

  .brand { position: absolute; left: 0; width: 100%; text-align: center; }
  .brand-name {
    position: absolute; left: 500px; top: 34px; width: 430px; text-align: center;
    font-family: "Lato", sans-serif; font-weight: 900; font-size: 72px; color: var(--sky); letter-spacing: 1px;
  }
  .brand-tagline {
    position: absolute; left: 505px; top: 118px; width: 430px; text-align: center;
    font-family: "Josefin Sans", sans-serif; font-size: 27px; color: var(--cream);
    font-variant: small-caps; letter-spacing: 2px; transform: rotate(4deg);
  }

  .artwork { position: absolute; }
  .artwork-tractor { left: 303px; top: 186px; width: 444px; height: 188px; border-radius: 40px; background: radial-gradient(ellipse at center, rgba(150,190,110,.75), rgba(90,140,70,.0) 72%); }
  .artwork-tipper { left: 778px; top: 173px; width: 287px; height: 243px; border-radius: 24px; background: radial-gradient(ellipse at center, rgba(190,200,180,.65), rgba(120,150,110,0) 75%); }
  .artwork-tipper-faint { left: 22px; top: 54px; width: 237px; height: 173px; border-radius: 20px; background: radial-gradient(ellipse at center, rgba(60,110,60,.5), rgba(60,110,60,0) 75%); }

  .panel { position: absolute; top: 422px; height: 275px; border-radius: 52px 52px 0 0; overflow: hidden; box-shadow: 0 6px 14px rgba(0,0,0,.35); }
  .panel-contact { left: 40px; width: 513px; }
  .panel-services { left: 641px; width: 512px; background: rgba(135,124,71,.92); }

  .contact-header { height: 115px; background: rgba(135,124,71,.92); text-align: center; padding-top: 4px; }
  .contact-name { font-family: "Lato", sans-serif; font-weight: 900; font-size: 32px; letter-spacing: 6px; color: var(--sky); }
  .contact-tagline { font-family: "Josefin Sans", sans-serif; font-style: italic; font-size: 15px; letter-spacing: 1.5px; color: var(--ink-green); margin-top: -2px; }
  .contact-town, .contact-abn { font-family: "Poppins", sans-serif; font-weight: 600; font-size: 16px; letter-spacing: 2px; color: var(--ink-green); line-height: 22px; }
  .contact-body { height: 160px; background: var(--panel-green); text-align: center; padding-top: 34px; color: var(--ink-green); font-family: "Poppins", sans-serif; font-weight: 600; }
  .contact-phone { font-size: 31px; letter-spacing: 1px; }
  .contact-phone .digits { letter-spacing: 5px; }
  .contact-email { font-size: 26px; margin-top: 18px; }

  .service-list { list-style: none; padding-top: 10px; }
  .service { display: flex; align-items: center; justify-content: center; height: 66px; font-family: "Roboto", sans-serif; font-style: italic; font-weight: 900; font-size: 30px; color: var(--ink-green); }
  .service-icon { width: 48px; height: 36px; margin-right: 6px; }

  .base-strip { position: absolute; left: 0; bottom: 0; width: 100%; height: 6px; background: var(--base-grey); }
</style>
</head>
<body>
<div class="card">
  <svg class="card-backdrop" width="1200" height="741" viewBox="0 0 1200 741">
    <defs>
      <radialGradient id="vignette" cx="50%" cy="35%" r="75%">
        <stop offset="0" stop-color="#000" stop-opacity="0"/>
        <stop offset="1" stop-color="#000" stop-opacity=".25"/>
      </radialGradient>
    </defs>
    <rect width="1200" height="741" fill="var(--field-green)"/>
    <path d="M140 0 Q605 215 1200 16 L1200 0 Z" fill="var(--rust)"/>
    <path d="M0 279 C320 330 760 360 1200 487 L1200 741 L0 741 Z" fill="var(--rust)"/>
    <path d="M0 279 C320 330 760 360 1200 487 L1200 420 C760 300 320 250 0 180 Z" fill="var(--band-green)" opacity=".55"/>
    <rect width="1200" height="741" fill="url(#vignette)"/>
  </svg>

  <div class="artwork artwork-tipper-faint" role="img" aria-label="Faint silhouette of a tipper truck cab"></div>
  <div class="artwork artwork-tractor" role="img" aria-label="Illustration of a tractor with a front end loader attachment"></div>
  <div class="artwork artwork-tipper" role="img" aria-label="Illustration of a 22 ton tipper truck"></div>

  <h1 class="brand-name">Dobbo's</h1>
  <p class="brand-tagline">Earthworks and tipper hire</p>

  <section class="panel panel-contact">
    <div class="contact-header">
      <div class="contact-name">Dobbo's</div>
      <div class="contact-tagline">small earthworks and tipper hire</div>
      <div class="contact-town">TOOWOOMBA</div>
      <div class="contact-abn">ABN:51603928174</div>
    </div>
    <div class="contact-body">
      <div class="contact-phone">Phone: <span class="digits">0412583906</span></div>
      <div class="contact-email">Email: dobbo.3@farrowpost.com</div>
    </div>
  </section>

  <section class="panel panel-services">
    <ul class="service-list">
      <li class="service">
        <svg class="service-icon" viewBox="0 0 48 36" role="img" aria-label="Tipper truck icon"><g fill="none" stroke="var(--ink-green)" stroke-width="3"><rect x="3" y="12" width="28" height="14"/><path d="M31 16 h8 l6 6 v4 h-14z"/><circle cx="11" cy="29" r="4"/><circle cx="38" cy="29" r="4"/></g></svg>
        Tipper hire
      </li>
      <li class="service">
        <svg class="service-icon" viewBox="0 0 48 36" role="img" aria-label="Tractor icon"><g fill="none" stroke="var(--ink-green)" stroke-width="3"><path d="M8 20 v-12 h14 l4 10 h14 v8"/><circle cx="13" cy="26" r="7"/><circle cx="38" cy="28" r="5"/></g></svg>
        Earthmoving
      </li>
      <li class="service">
        <svg class="service-icon" viewBox="0 0 48 36" role="img" aria-label="Grass icon"><g fill="none" stroke="var(--ink-green)" stroke-width="3"><path d="M8 34 Q8 16 2 4"/><path d="M18 34 Q18 14 26 2"/><path d="M28 34 Q30 18 42 8"/><path d="M13 34 Q12 22 10 14"/></g></svg>
        Grass slashing
      </li>
      <li class="service">
        <svg class="service-icon" viewBox="0 0 48 36" role="img" aria-label="Fire icon"><g fill="none" stroke="var(--ink-green)" stroke-width="3"><circle cx="24" cy="18" r="15"/><path d="M24 8 C30 14 30 20 27 25 H21 C18 20 20 14 24 8Z" fill="var(--ink-green)"/></g></svg>
        Fire hazard reduction
      </li>
    </ul>
  </section>

  <div class="base-strip"></div>
</div>
</body>
</html>
```